Brindlewick Solutions Ltd

I'd like to create a company letterhead for the attached logo in word format.

I'd like to emphasis the icon in large translucent state from the left corner and ensure that the letterhead colouring matches the colour palette of the current logo with a contrast so it's clear to see. I've attached a copy of our sister company page on the app for reference.

```html
<!DOCTYPE html>
<html lang="en">
<head>
<meta charset="utf-8">
<title>Brindlewick Solutions Ltd — Letterhead</title>
<link href="https://fonts.googleapis.com/css2?family=Montserrat:wght@400&family=Roboto:wght@400&display=swap" rel="stylesheet">
<style>
  :root {
    --backdrop: #dcdcdc;
    --paper: #f8f8f8;
    --teal: #17b3a0;
    --teal-wash: #e7f2f1;
    --ink-grey: #6b6b6b;
    --rule-grey: #9a9a9a;
    --white: #ffffff;
  }
  * { margin: 0; padding: 0; box-sizing: border-box; }
  html, body {
    width: 1153px;
    height: 1200px;
    overflow: hidden;
    background: var(--backdrop);
  }
  .letterhead {
    position: absolute;
    left: 168px;
    top: 30px;
    width: 817px;
    height: 1140px;
    background: var(--paper);
    box-shadow: 0 10px 30px rgba(0,0,0,0.12);
    overflow: hidden;
  }
  .watermark {
    position: absolute;
    left: 0;
    top: 0;
    width: 817px;
    height: 1140px;
  }
  .brand {
    position: absolute;
    left: 60px;
    top: 58px;
    width: 220px;
    text-align: center;
  }
  .brand-dot {
    display: block;
    width: 66px;
    height: 66px;
    margin: 0 auto 10px;
    border-radius: 50%;
    background: var(--teal);
  }
  .brand-name {
    font-family: 'Montserrat', sans-serif;
    font-weight: 400;
    font-size: 32px;
    line-height: 1;
    color: var(--teal);
  }
  .brand-tagline {
    font-family: 'Montserrat', sans-serif;
    font-weight: 400;
    font-size: 10px;
    letter-spacing: 7.4px;
    color: var(--ink-grey);
    margin-top: 6px;
    padding-left: 7px;
  }
  .contact {
    position: absolute;
    left: 535px;
    top: 68px;
    font-family: 'Roboto', sans-serif;
    font-style: normal;
    font-size: 17px;
    line-height: 21px;
    color: var(--ink-grey);
  }
  .contact-address { margin-bottom: 6px; }
  .contact-line {
    display: flex;
    align-items: center;
    gap: 6px;
  }
  .contact-line svg { flex: none; }
  .footer-band {
    position: absolute;
    left: 0;
    bottom: 0;
    width: 817px;
    height: 36px;
  }
  .footer-web {
    position: absolute;
    right: 55px;
    bottom: 11px;
    font-family: 'Roboto', sans-serif;
    font-size: 17px;
    color: var(--white);
  }
</style>
</head>
<body>
  <main class="letterhead">
    <svg class="watermark" viewBox="0 0 817 1140" aria-hidden="true">
      <circle cx="150" cy="645" r="400" fill="var(--teal-wash)"/>
    </svg>

    <header class="brand">
      <span class="brand-dot"></span>
      <div class="brand-name">Brindlewick</div>
      <div class="brand-tagline">SOLUTIONS LTD</div>
    </header>

    <address class="contact">
      <div class="contact-address">
        Brindlewick Solutions Ltd<br>
        48 Larkspur Ave Suite<br>
        7 Fairhaven, OR 97410
      </div>
      <div class="contact-line">
        <svg width="15" height="12" viewBox="0 0 15 12" aria-hidden="true">
          <path d="M1 4 Q7.5 -1 14 4 L12 5.5 L10 3.5 L5 3.5 L3 5.5 Z" fill="var(--teal)"/>
          <path d="M4 6 L11 6 L13 11 L2 11 Z" fill="var(--teal)"/>
        </svg>
        1-800-555-0147
      </div>
      <div class="contact-line">
        <svg width="15" height="11" viewBox="0 0 15 11" aria-hidden="true">
          <rect x="0.5" y="0.5" width="14" height="10" fill="var(--teal)"/>
          <path d="M1 1 L7.5 6 L14 1 M1 10 L5.5 5 M14 10 L9.5 5" stroke="var(--white)" stroke-width="1.1" fill="none"/>
        </svg>
        hello@brindlewick.co
      </div>
    </address>

    <svg class="footer-band" viewBox="0 0 817 36" aria-hidden="true">
      <path d="M0 9 L527 9 Q518 14 505 15 L0 15 Z" fill="var(--rule-grey)"/>
      <path d="M0 24 L500 24 Q520 24 540 12 Q556 2 575 1 L817 1 L817 36 L0 36 Z" fill="var(--teal)"/>
    </svg>
    <div class="footer-web">www.brindlewick.co</div>
  </main>
</body>
</html>
```